Real estate broker business card

Want a modern celan but effective business card for my residential and commercial real estate business. I want the back of the card to advertise my services and to capture business. I have attached the back of my current business card fore ideas
Updates

Logos, photo and text updates added! Added Saturday, September 3, 2016

Project Deadline Extended Reason: LOGOS, PHOTOS AND TEST JUST UPLOADED! I'M READY TO PICK A DESIGN! THANK YOU! Added Saturday, September 3, 2016

Target Market(s)

home buyers and seller. commercial buyers and sellers

Industry/Entity Type

Real Estate

Contact Information for Business Card

must have my contact information and my photo

Requirements
Must have
• Carla Ventrino
• Owner & Qualifying Broker
• Ventrino Real Estate Services
• 505.718.2094
• carla@ventrinohomes.example
• www.ventrinohomes.example
Nice to have
• metallic
• Business capture text: " Don't buy or lease property without someone looking out for your best interests. I will represent you on your home or investment purchase for FREE!"
• "Home owners, call today to receive a FREE market analysis for your homes value!

```html
<!DOCTYPE html>
<html lang="en">
<head>
<meta charset="utf-8">
<title>Ventrino Real Estate Services — Business Card</title>
<link rel="stylesheet" href="https://fonts.googleapis.com/css2?family=Source+Sans+3:ital,wght@0,400;0,600;1,400&display=swap">
<style>
  :root {
    --backdrop: #141414;
    --card: #ffffff;
    --teal: #0f6b78;
    --ink-grey: #555a5e;
    --rule: #b9bcbf;
  }
  * { box-sizing: border-box; margin: 0; padding: 0; }
  html, body {
    width: 1200px; height: 900px; overflow: hidden;
    background: var(--backdrop);
    font-family: "Source Sans 3", "Myriad Pro", Arial, sans-serif;
  }
  .canvas { position: relative; width: 1200px; height: 900px; }
  .card {
    position: absolute; top: 306px;
    width: 440px; height: 271px;
    background: var(--card);
    border-radius: 10px;
  }
  .card--front { left: 149px; }
  .card--back { left: 608px; }

  /* Front */
  .front-mark {
    position: absolute; left: 196px; top: 0; width: 0;
  }
  .brand-word {
    position: absolute; left: 50px; top: 118px;
    width: 140px; text-align: center;
    color: var(--teal); font-weight: 600; font-size: 26px; letter-spacing: .5px;
  }
  .brand-square {
    position: absolute; left: 106px; top: 86px;
    width: 26px; height: 26px; background: var(--teal);
  }
  .divider {
    position: absolute; left: 195px; top: 87px;
    width: 1px; height: 96px; background: var(--rule);
  }
  .person {
    position: absolute; left: 218px; top: 78px;
  }
  .person__name { color: var(--teal); font-weight: 600; font-size: 15.5px; line-height: 20px; }
  .person__title { color: var(--ink-grey); font-size: 12px; line-height: 14px; }
  .contacts {
    position: absolute; left: 218px; top: 142px; list-style: none;
  }
  .contacts li {
    display: flex; align-items: center; gap: 6px;
    color: var(--ink-grey); font-size: 12.5px; line-height: 16px;
  }
  .contacts svg { width: 9px; height: 9px; fill: var(--teal); flex: none; }

  /* Back */
  .back-brand {
    position: absolute; left: 0; top: 38px; width: 440px;
    display: flex; align-items: center; justify-content: center; gap: 12px;
    color: var(--teal); font-weight: 600;
  }
  .back-brand__square { width: 56px; height: 56px; background: var(--teal); }
  .back-brand__name { font-size: 40px; line-height: 40px; letter-spacing: 1px; }
  .back-brand__sub { font-size: 14px; line-height: 18px; letter-spacing: 2.5px; text-transform: uppercase; }
  .pitch {
    position: absolute; left: 0; top: 148px; width: 440px;
    text-align: center; color: var(--teal); font-size: 13px; line-height: 16px;
  }
  .offer {
    position: absolute; left: 0; top: 206px; width: 440px;
    text-align: center; color: var(--ink-grey); font-style: italic; font-size: 12.5px; line-height: 16px;
  }
</style>
</head>
<body>
<main class="canvas">
  <section class="card card--front" aria-label="Business card front">
    <div class="brand-square"></div>
    <div class="brand-word">Ventrino</div>
    <div class="divider"></div>
    <div class="person">
      <h1 class="person__name">Carla Ventrino</h1>
      <p class="person__title">Owner &amp; Qualifying Broker</p>
    </div>
    <ul class="contacts">
      <li><svg viewBox="0 0 10 10"><path d="M2 0.5l2 2-1 1.2c.6 1.3 1.6 2.3 2.9 2.9l1.2-1 2 2-1.2 1.7C4.5 9.3.7 5.5.3 1.7z"/></svg>505.718.2094</li>
      <li><svg viewBox="0 0 10 10"><path d="M0 2h10v6H0z M0 2l5 3.5L10 2" /><path d="M0.8 2.6L5 5.5l4.2-2.9" stroke="#fff" stroke-width=".8" fill="none"/></svg>carla@ventrinohomes.example</li>
      <li><svg viewBox="0 0 10 10"><circle cx="5" cy="5" r="4.6"/><path d="M5 .4v9.2M.4 5h9.2M5 .4c-2.4 2.6-2.4 6.6 0 9.2M5 .4c2.4 2.6 2.4 6.6 0 9.2" stroke="#fff" stroke-width=".6" fill="none"/></svg>www.ventrinohomes.example</li>
    </ul>
  </section>

  <section class="card card--back" aria-label="Business card back">
    <div class="back-brand">
      <div class="back-brand__square"></div>
      <div>
        <div class="back-brand__name">VENTRINO</div>
        <div class="back-brand__sub">Real Estate Services</div>
      </div>
    </div>
    <p class="pitch">Don't buy or lease property without someone looking<br>out for your best interests. I will represent you on<br>your home or investment purchase for FREE!</p>
    <p class="offer">Home owners, call today to receive a<br>FREE market analysis for your homes value!</p>
  </section>
</main>
</body>
</html>
```